Business card for a Exhibition booth fabrication company

Hi. My company would like to change our corporate name card. We are an events and Exhibition stand builder company. We would like our corporate name card to resonate what we do. I need someone to create something unique that relates to the industry that I am in. The graphic designer should be creative to incorporate the elements of my industry and try to blend in well in the design of the card. Our aim is to ensure that we are unique and our card can look different from our competitors.
Updates

Target Market(s)

Marketing and events manager from all companies

Contact Information for Business Card

The business card should have the following details:
Name
Job Title
Email
Website

Colors

Designer to choose colors to be used in the design.

Requirements
Must have
• The card must be look something that is relevant to the service that I am providing. My website is: www.velmora-buildworks.com
• You can see my website to get more information on what service that I am doing
Nice to have
• On the back of my card, I would like to have a globe image with the incorporation of my company logo. This is to indicate that my services can be done in any part of the world.

```html
<!DOCTYPE html>
<html lang="en">
<head>
<meta charset="utf-8">
<title>Velmora Buildworks – Business Card</title>
<link rel="stylesheet" href="https://fonts.googleapis.com/css2?family=Montserrat:wght@500;600&family=Open+Sans:wght@400;600&display=swap">
<style>
  :root {
    --backdrop: #d9d9db;
    --red-light: #e8202c;
    --red-mid: #c8121d;
    --red-dark: #7d0a12;
    --white: #ffffff;
    --ink-grey: #5b5b5d;
    --ink-dark: #333335;
    --accent: #e31b23;
  }
  * { box-sizing: border-box; margin: 0; padding: 0; }
  html, body {
    width: 1200px; height: 900px; overflow: hidden;
    background: var(--backdrop);
  }
  .stage { position: relative; width: 1200px; height: 900px; }

  .card {
    position: absolute;
    width: 540px; height: 310px;
    border-radius: 26px;
    overflow: hidden;
    box-shadow: 0 6px 18px rgba(0,0,0,0.18);
  }

  /* Back side */
  .card-back {
    left: 70px; top: 130px;
    background: linear-gradient(180deg, var(--red-light) 0%, var(--red-mid) 55%, var(--red-dark) 100%);
    color: var(--white);
    text-align: center;
  }
  .globe-area {
    position: absolute; left: 40px; top: 20px; width: 460px; height: 250px;
    border-radius: 40%;
    background: radial-gradient(ellipse at center, rgba(255,255,255,0.16) 0%, rgba(255,255,255,0.06) 55%, rgba(255,255,255,0) 75%);
  }
  .back-title {
    position: relative;
    margin-top: 92px;
    font-family: 'Montserrat', sans-serif;
    font-weight: 600; font-size: 24px; letter-spacing: 4px;
  }
  .service-list {
    position: relative;
    margin-top: 16px;
    list-style: none;
    font-family: 'Open Sans', sans-serif;
    font-size: 14px; line-height: 21px;
  }
  .service-list .sep {
    display: inline-block; width: 6px; height: 6px; border-radius: 50%;
    background: var(--white); margin: 0 7px; vertical-align: middle;
  }

  /* Front side */
  .card-front {
    left: 590px; top: 460px;
    background: var(--white);
  }
  .brand-name {
    position: absolute; left: 34px; top: 58px;
    font-family: 'Montserrat', sans-serif;
    font-weight: 600; font-size: 24px; letter-spacing: 3px;
    color: var(--ink-grey);
  }
  .person { position: absolute; left: 34px; top: 130px; }
  .person-name {
    font-family: 'Montserrat', sans-serif;
    font-weight: 600; font-size: 22px; letter-spacing: 1px;
    color: var(--accent);
  }
  .person-title {
    font-family: 'Open Sans', sans-serif;
    font-size: 14px; color: var(--ink-dark); margin-top: 2px;
  }
  .contact-list {
    position: absolute; left: 34px; top: 200px;
    list-style: none;
    font-family: 'Open Sans', sans-serif;
    font-size: 14px; line-height: 22px; color: var(--ink-dark);
  }
  .contact-list li { display: flex; align-items: center; gap: 8px; }
  .contact-list svg { width: 14px; height: 14px; flex: none; }
</style>
</head>
<body>
<main class="stage">

  <section class="card card-back" aria-label="Card back">
    <div class="globe-area" role="img" aria-label="Dotted world map"></div>
    <h2 class="back-title">VELMORA BUILDWORKS</h2>
    <ul class="service-list">
      <li>Exhibition Booth Fabrication<span class="sep"></span>Outdoor Booth Setup</li>
      <li>Interior Design<span class="sep"></span>Installation and Dismantle</li>
      <li>Exhibition Management<span class="sep"></span>Shell Scheme Display Booth</li>
      <li>Custom Stand Design<span class="sep"></span>Exhibition Furniture and Equipment</li>
      <li>Exhibition Project Management</li>
    </ul>
  </section>

  <section class="card card-front" aria-label="Card front">
    <h1 class="brand-name">VELMORA BUILDWORKS</h1>
    <div class="person">
      <p class="person-name">DANIEL HART</p>
      <p class="person-title">Managing Director</p>
    </div>
    <ul class="contact-list">
      <li>
        <svg viewBox="0 0 16 16" aria-hidden="true"><path fill="#e31b23" d="M3 1h3l1 4-2 1c1 2 3 4 5 5l1-2 4 1v3c0 1-1 2-2 2C7 15 1 9 1 3c0-1 1-2 2-2z"/></svg>
        +65 81402276 (Singapore)
      </li>
      <li>
        <svg viewBox="0 0 16 16" aria-hidden="true"><path fill="#e31b23" d="M3 1h3l1 4-2 1c1 2 3 4 5 5l1-2 4 1v3c0 1-1 2-2 2C7 15 1 9 1 3c0-1 1-2 2-2z"/></svg>
        +974 55218407 (Qatar)
      </li>
      <li>
        <svg viewBox="0 0 16 16" aria-hidden="true"><rect x="1" y="3" width="14" height="10" rx="1" fill="#e31b23"/><path d="M1.5 4l6.5 5 6.5-5" stroke="#fff" stroke-width="1.3" fill="none"/></svg>
        info@www.velmora-buildworks.com
      </li>
      <li>
        <svg viewBox="0 0 16 16" aria-hidden="true"><circle cx="8" cy="8" r="7" fill="#e31b23"/><path d="M1.5 8h13M8 1.5c-3 3.5-3 9.5 0 13M8 1.5c3 3.5 3 9.5 0 13" stroke="#fff" stroke-width="1" fill="none"/></svg>
        www.velmora-buildworks.com
      </li>
    </ul>
  </section>

</main>
</body>
</html>
```